Business Card Design for company

We want new business cards. We'd like something different-- yet still highly professional. Our tagline is Providing leadership, delivering success. Stock photos are ok, as long as they are relevant and look upscale.

Target Market(s)

Architecture/Business Management Consulting/Engineering Consulting

Contact Information for Business Card

dark gray background with pops of blue might be good, but you tell me. You're the designers. Rounded corners might be nice, but again, you tell me.

Font styles to use
Serif
Sans Serif

Colors
3276b5
5c5c5c
9d9d9d
fbfbfb

Requirements
Nice to have
• Something different, but still very professional.

```html
<!DOCTYPE html>
<html lang="en">
<head>
<meta charset="utf-8">
<title>Norvale Partners — Business Card</title>
<link href="https://fonts.googleapis.com/css2?family=Montserrat:wght@400;500;600;700&display=swap" rel="stylesheet">
<style>
  :root {
    --blue: #3276b5;
    --blue-deep: #2a5f95;
    --slate: #4a4e57;
    --slate-dark: #3f434b;
    --grey: #5c5c5c;
    --grey-light: #9d9d9d;
    --paper: #fbfbfb;
    --backdrop: #c9cacc;
  }
  * { box-sizing: border-box; margin: 0; padding: 0; }
  html, body {
    width: 1200px; height: 930px; overflow: hidden;
    background: var(--backdrop);
    font-family: "Montserrat", Arial, sans-serif;
  }
  .canvas { position: relative; width: 1200px; height: 930px; }

  .card {
    position: absolute;
    width: 630px; height: 360px;
    border-radius: 26px;
    box-shadow: 0 10px 24px rgba(0,0,0,.22);
    overflow: hidden;
  }

  /* Front */
  .card-front {
    left: 90px; top: 70px;
    background: linear-gradient(135deg, var(--slate) 0%, var(--slate-dark) 100%);
    display: flex; flex-direction: column; align-items: center; justify-content: center;
  }
  .front-name {
    color: var(--paper);
    font-weight: 700; font-size: 46px; letter-spacing: 3px;
    display: flex; align-items: center; gap: 14px;
  }
  .front-name .mark {
    width: 20px; height: 20px; background: var(--blue); display: inline-block;
  }
  .front-web {
    margin-top: 56px;
    display: flex; align-items: center; gap: 12px;
    color: var(--paper); font-size: 15px; letter-spacing: .5px;
  }
  .front-web .rule { width: 110px; height: 1px; background: var(--grey-light); }

  /* Back */
  .card-back {
    left: 480px; top: 500px;
    background: var(--paper);
    color: var(--grey);
  }
  .back-brand {
    position: absolute; left: 44px; top: 62px;
    color: var(--slate-dark);
    font-weight: 700; font-size: 30px; letter-spacing: 2px; line-height: 1.15;
    display: flex; align-items: center; gap: 12px;
  }
  .back-brand .mark { width: 16px; height: 16px; background: var(--blue); display: inline-block; }

  .person { position: absolute; right: 44px; top: 50px; text-align: right; }
  .person-name { color: var(--blue); font-weight: 600; font-size: 26px; letter-spacing: 1px; }
  .person-role { font-size: 13px; color: var(--grey); margin-top: 2px; }
  .rule-top {
    position: absolute; right: 44px; top: 118px; width: 300px; height: 2px; background: var(--blue-deep);
  }
  .address {
    position: absolute; right: 44px; top: 140px; text-align: right;
    font-size: 14px; line-height: 1.55;
  }
  .rule-bottom {
    position: absolute; left: 44px; top: 238px; width: 280px; height: 2px; background: var(--blue-deep);
  }
  .contacts {
    position: absolute; left: 44px; top: 256px;
    list-style: none; font-size: 15px; line-height: 1.6;
  }
  .contacts li { display: flex; align-items: center; gap: 10px; }
  .contacts svg { width: 12px; height: 12px; fill: var(--blue); flex: none; }
  .contacts .accent { color: var(--blue); }
</style>
</head>
<body>
<div class="canvas">

  <section class="card card-front" aria-label="Card front">
    <div class="front-name"><span class="mark"></span>NORVALE PARTNERS</div>
    <div class="front-web"><span class="rule"></span>www.norvalepartners.com<span class="rule"></span></div>
  </section>

  <section class="card card-back" aria-label="Card back">
    <div class="back-brand"><span class="mark"></span>NORVALE<br>PARTNERS</div>

    <div class="person">
      <div class="person-name">DANIEL HART</div>
      <div class="person-role">Director</div>
    </div>
    <div class="rule-top"></div>
    <address class="address" style="font-style:normal">
      48b Harbour Lane,<br>Westford, NZ, 8020
    </address>

    <div class="rule-bottom"></div>
    <ul class="contacts">
      <li>
        <svg viewBox="0 0 24 24" aria-hidden="true"><path d="M6.6 10.8a15 15 0 0 0 6.6 6.6l2.2-2.2a1 1 0 0 1 1-.25 11.4 11.4 0 0 0 3.6.57 1 1 0 0 1 1 1V20a1 1 0 0 1-1 1A17 17 0 0 1 3 4a1 1 0 0 1 1-1h3.5a1 1 0 0 1 1 1c0 1.25.2 2.45.57 3.57a1 1 0 0 1-.25 1z"/></svg>
        (555) 014-2870
      </li>
      <li>
        <svg viewBox="0 0 24 24" aria-hidden="true"><path d="M2 5h20v14H2zm2 2v.5l8 5 8-5V7zm0 2.8V17h16V9.8l-8 5z"/></svg>
        info@norvalepartners.com
      </li>
      <li>
        <svg viewBox="0 0 24 24" aria-hidden="true"><circle cx="12" cy="12" r="10"/></svg>
        <span>www.<span class="accent">norvalepartners</span>.com</span>
      </li>
    </ul>
  </section>

</div>
</body>
</html>
```